Business card design for holistic health care clinic

We need a double-sided business card design for our holistic health care clinic that integrates our logo design and also its color scheme. My business is called Valmira. It is an integrative medicine clinic. You have already done the logo for me. Please ensure an elegant and upscale design that is not cluttered, but still has all the necessary information (please see below for details).

Target Market(s)

Wellness, fitness, rehabilitation for educated, well-traveled open-minded clients who are focused on natural, organic, balanced and preventive healthcare and lifestyle.

Industry/Entity Type

Medical

Contact Information for Business Card

Modern, clean.

Number of Pages Required

1 page

Font styles to use
Serif
Sans Serif

Colors

Designer to choose colors to be used in the design.

Requirements
Must have
• Logo on one side, all other information on the other side.
• Other information should include:
• Tobias Wrenfeld - DOE, CPT, LMT
• 4100 East Marrow Drive
• Austin, TX 78119
• 512 555 0148
• 818 555 0192
• info@ValmiraHealth.example
• t.wrenfeld@ValmiraHealth.example
Nice to have
• Darker background on front - but not totally black - shaded/dark gray.

```html
<!DOCTYPE html>
<html lang="en">
<head>
<meta charset="utf-8">
<title>Valmira – Business Card</title>
<link rel="stylesheet" href="https://fonts.googleapis.com/css2?family=Montserrat:wght@400;600;700&family=Lato:wght@400;700&display=swap">
<style>
  :root {
    --backdrop: #e9e7e4;
    --card-blue: #129bdb;
    --card-dark: #1c1f22;
    --brand-blue: #1b9ad6;
    --text-light: #ffffff;
  }
  * { box-sizing: border-box; margin: 0; padding: 0; }
  html, body { width: 1200px; height: 900px; overflow: hidden; }
  body {
    position: relative;
    background: var(--backdrop);
    font-family: "Lato", sans-serif;
  }
  .card {
    position: absolute;
    box-shadow: 0 6px 18px rgba(0,0,0,0.18);
  }
  .card--contact {
    left: 78px; top: 34px; width: 587px; height: 364px;
    background: var(--card-blue);
    color: var(--text-light);
  }
  .holder-name {
    position: absolute; left: 28px; top: 86px;
    font-family: "Montserrat", sans-serif;
    font-weight: 700; font-size: 18px; letter-spacing: 0.3px;
    white-space: nowrap;
  }
  .holder-name .credentials {
    font-weight: 400; font-size: 14.5px; margin-left: 6px;
  }
  .address {
    position: absolute; left: 28px; top: 178px;
    font-size: 16px; line-height: 21px;
  }
  .contact-list {
    position: absolute; left: 28px; top: 230px;
    list-style: none;
    font-size: 15.5px; line-height: 21.5px;
  }
  .contact-list li { display: flex; align-items: center; }
  .contact-list svg { width: 12px; height: 12px; margin-right: 9px; fill: var(--text-light); flex: none; }
  .card--brand {
    left: 388px; top: 505px; width: 567px; height: 352px;
    background: var(--card-dark);
    color: var(--brand-blue);
    text-align: center;
  }
  .brand-name {
    position: absolute; left: 0; right: 0; top: 153px;
    font-family: "Montserrat", sans-serif;
    font-weight: 700; font-size: 50px; letter-spacing: 1px;
    line-height: 1;
  }
  .brand-tagline {
    position: absolute; left: 0; right: 0; top: 210px;
    font-family: "Montserrat", sans-serif;
    font-weight: 600; font-size: 15.5px;
  }
</style>
</head>
<body>
  <section class="card card--contact">
    <h1 class="holder-name">TOBIAS WRENFELD<span class="credentials">DOE, CPT, LMT</span></h1>
    <p class="address">4100 East Marrow Drive<br>Austin, TX 78119</p>
    <ul class="contact-list">
      <li><svg viewBox="0 0 12 12"><path d="M1 4c0-2 2-3 5-3s5 1 5 3H8.5V3h-5v1zM2 6l2-2h4l2 2v5H2z"/></svg>512 555 0148</li>
      <li><svg viewBox="0 0 12 12"><path d="M3 0h6v12H3zM4 1.5v8h4v-8z"/></svg>818 555 0192</li>
      <li><svg viewBox="0 0 12 12"><path d="M0 2h12v8H0zM1 3v.5l5 3.5 5-3.5V3z"/></svg>info@ValmiraHealth.example</li>
      <li><svg viewBox="0 0 12 12"><path d="M0 2h12v8H0zM1 3v.5l5 3.5 5-3.5V3z"/></svg>t.wrenfeld@ValmiraHealth.example</li>
      <li><svg viewBox="0 0 12 12"><circle cx="6" cy="6" r="6"/></svg>www.ValmiraHealth.example</li>
    </ul>
  </section>

  <section class="card card--brand">
    <p class="brand-name">VALMIRA</p>
    <p class="brand-tagline">Integrative Holistic Medicine</p>
  </section>
</body>
</html>
```